TA BRAMLEY BUSINESS CARD DESIGN PROJECT

We need to utilize our logo that was expertly created on PixelHarbor and now need to match this with a business card design.

```html
<!DOCTYPE html>
<html lang="en">
<head>
<meta charset="utf-8">
<title>TA Bramley Business Card</title>
<link href="https://fonts.googleapis.com/css2?family=Lato:wght@400;700;900&display=swap" rel="stylesheet">
<style>
  :root {
    --brand-blue: #0152aa;
    --card-white: #ffffff;
    --ink-grey: #555555;
    --stage: #2e2e2e;
  }
  * { margin: 0; padding: 0; box-sizing: border-box; }
  html, body { width: 1200px; height: 875px; overflow: hidden; }
  body {
    background: var(--stage);
    font-family: "Lato", sans-serif;
    position: relative;
  }
  .card {
    position: absolute;
    width: 560px;
    height: 320px;
    border-radius: 22px;
    overflow: hidden;
  }
  .card-front {
    left: 50px; top: 90px;
    background: var(--brand-blue);
    display: flex; align-items: center; justify-content: center;
  }
  .card-back {
    left: 590px; top: 465px;
    background: var(--card-white);
  }
  .wordmark {
    display: flex; align-items: center; gap: 14px;
    font-weight: 900;
    letter-spacing: 0.12em;
    color: var(--card-white);
    font-size: 46px;
  }
  .wordmark-dot {
    width: 34px; height: 34px; border-radius: 50%;
    background: var(--card-white);
  }
  .card-back .wordmark {
    position: absolute; left: 40px; top: 78px;
    color: var(--brand-blue); font-size: 36px; gap: 12px;
  }
  .card-back .wordmark-dot { background: var(--brand-blue); width: 26px; height: 26px; }
  .back-band { position: absolute; inset: 0; }
  .holder {
    position: absolute; left: 40px; bottom: 42px;
  }
  .holder-name {
    color: var(--brand-blue); font-weight: 700; font-size: 22px; letter-spacing: 0.02em;
  }
  .holder-role { color: var(--ink-grey); font-size: 17px; margin-top: 2px; }
  .contact {
    position: absolute; right: 24px; top: 92px;
    list-style: none;
    color: var(--card-white); font-size: 13.5px; line-height: 20px;
    text-align: right;
  }
  .contact li { display: flex; justify-content: flex-end; align-items: center; gap: 8px; }
  .contact svg { width: 11px; height: 11px; fill: var(--card-white); flex: none; }
  .contact .no-icon { width: 11px; }
</style>
</head>
<body>
  <section class="card card-front" aria-label="Card front">
    <div class="wordmark"><span class="wordmark-dot"></span>TA BRAMLEY</div>
  </section>

  <section class="card card-back" aria-label="Card back">
    <svg class="back-band" viewBox="0 0 560 320" preserveAspectRatio="none" aria-hidden="true">
      <polygon points="345,0 560,0 560,320 405,320" fill="var(--brand-blue)"/>
    </svg>
    <div class="wordmark"><span class="wordmark-dot"></span>TA BRAMLEY</div>
    <div class="holder">
      <div class="holder-name">DANIEL REEVE</div>
      <div class="holder-role">Founder &amp; CEO</div>
    </div>
    <ul class="contact">
      <li>123 Anywhere St <svg viewBox="0 0 10 10"><path d="M5 0a3.5 3.5 0 0 0-3.5 3.5C1.5 6 5 10 5 10s3.5-4 3.5-6.5A3.5 3.5 0 0 0 5 0zm0 5a1.5 1.5 0 1 1 0-3 1.5 1.5 0 0 1 0 3z"/></svg></li>
      <li>Any City, ST 12345 <span class="no-icon"></span></li>
      <li>(123) 456-7890 <svg viewBox="0 0 10 10"><path d="M2 0l2 2.5-1 1.2a6 6 0 0 0 3.3 3.3l1.2-1L10 8l-1.5 2C4 10 0 6 0 1.5z"/></svg></li>
      <li>(231) 456-7890 <svg viewBox="0 0 10 10"><rect x="2.5" y="0" width="5" height="10" rx="1"/></svg></li>
      <li>(312) 456-7890 <svg viewBox="0 0 10 10"><rect x="2" y="0" width="6" height="3"/><rect x="0" y="3.5" width="10" height="4" rx="1"/><rect x="2" y="7" width="6" height="3"/></svg></li>
      <li>hello@tabramley.com <svg viewBox="0 0 10 10"><path d="M0 2h10v6H0z M0 2l5 3.5L10 2" stroke="#0152aa" stroke-width="0.8"/></svg></li>
      <li>www.tabramley.com <svg viewBox="0 0 10 10"><circle cx="5" cy="5" r="5"/></svg></li>
    </ul>
  </section>
</body>
</html>
```